Awesome photographers card for an awesome new business

Double sided business card Black background and silver logo in middle on one side. Details on otherside. please keep it simple

Industry/Entity Type

Photographer

Contact Information for Business Card

Gerald Fenwick
0452817360
GeraldFenwickPhotography47@mailbox.test
www.GeraldFenwickPhotography.test.au
Instagram _Gerald_fenwick

Requirements
Must have
• My logo in Silver
• please use instagram logo instead of "Instagram"

```html
<!DOCTYPE html>
<html lang="en">
<head>
<meta charset="utf-8">
<title>Gerald Fenwick Photography – Business Card</title>
<link rel="stylesheet" href="https://fonts.googleapis.com/css2?family=Montserrat:wght@700&family=Questrial&display=swap">
<style>
  :root {
    --backdrop: #e9e7e3;
    --card-white: #f7f7f7;
    --grey-light: #b9b9b9;
    --grey-mid: #8d8d8d;
    --grey-dark: #6e6e6e;
    --ink-white: #ffffff;
    --card-black: #1e1f1f;
    --silver: #a7a7a7;
    --silver-light: #d6d6d6;
  }
  html, body {
    margin: 0;
    padding: 0;
    width: 1200px;
    height: 911px;
    overflow: hidden;
    background: var(--backdrop);
  }
  .canvas {
    position: relative;
    width: 1200px;
    height: 911px;
  }
  .card {
    position: absolute;
    top: 128px;
    width: 400px;
    height: 655px;
    border-radius: 26px;
    overflow: hidden;
    box-shadow: 0 18px 40px rgba(0,0,0,0.22);
  }
  .card--details {
    left: 160px;
    background: linear-gradient(160deg, var(--grey-light) 0%, var(--grey-mid) 45%, var(--grey-dark) 100%);
  }
  .card--logo {
    left: 640px;
    background: var(--card-black);
  }
  .details__cap {
    position: absolute;
    left: 50%;
    top: -330px;
    width: 560px;
    height: 560px;
    margin-left: -280px;
    border-radius: 50%;
    background: var(--card-white);
  }
  .brand {
    position: absolute;
    left: 0;
    right: 0;
    display: flex;
    flex-direction: column;
    align-items: center;
    font-family: "Questrial", sans-serif;
    text-align: center;
    letter-spacing: 0.22em;
    text-transform: uppercase;
  }
  .brand__dot {
    width: 12px;
    height: 12px;
    border-radius: 50%;
    margin-bottom: 14px;
  }
  .brand__name {
    font-size: 22px;
    line-height: 1.5;
  }
  .card--details .brand { top: 70px; color: var(--silver); }
  .card--details .brand__dot { background: var(--silver); }
  .card--logo .brand { top: 270px; color: var(--silver-light); }
  .card--logo .brand__dot { background: var(--silver-light); }

  .details__body {
    position: absolute;
    left: 0;
    right: 0;
    top: 300px;
    text-align: center;
    color: var(--ink-white);
    font-family: "Questrial", sans-serif;
  }
  .details__name {
    font-family: "Montserrat", sans-serif;
    font-weight: 700;
    font-size: 23px;
    letter-spacing: 0.02em;
    text-transform: uppercase;
    margin: 0 0 30px;
  }
  .contact {
    list-style: none;
    margin: 0;
    padding: 0;
  }
  .contact__item {
    display: flex;
    flex-direction: column;
    align-items: center;
    margin-bottom: 6px;
    font-size: 15.5px;
    line-height: 1.35;
  }
  .contact__icon {
    width: 13px;
    height: 13px;
    margin-bottom: 3px;
  }
  .contact__social-mark {
    width: 11px;
    height: 11px;
    margin-bottom: 4px;
    background: var(--ink-white);
    border-radius: 2px;
  }
</style>
</head>
<body>
<main class="canvas">
  <section class="card card--details" aria-label="Business card, details side">
    <div class="details__cap"></div>
    <div class="brand">
      <span class="brand__dot"></span>
      <span class="brand__name">Gerald Fenwick<br>Photography</span>
    </div>
    <div class="details__body">
      <h1 class="details__name">Gerald Fenwick</h1>
      <ul class="contact">
        <li class="contact__item">
          <svg class="contact__icon" viewBox="0 0 24 24" aria-hidden="true"><path fill="#fff" d="M6.6 10.8a15.1 15.1 0 0 0 6.6 6.6l2.2-2.2c.3-.3.7-.4 1-.2 1.1.4 2.3.6 3.6.6.6 0 1 .4 1 1V20c0 .6-.4 1-1 1A17 17 0 0 1 3 4c0-.6.4-1 1-1h3.5c.6 0 1 .4 1 1 0 1.3.2 2.5.6 3.6.1.3 0 .7-.2 1z"/></svg>
          <span>0452817360</span>
        </li>
        <li class="contact__item">
          <svg class="contact__icon" viewBox="0 0 24 24" aria-hidden="true"><rect x="2" y="5" width="20" height="14" rx="1.5" fill="#fff"/><path d="M2.5 6l9.5 7 9.5-7" fill="none" stroke="#8d8d8d" stroke-width="1.6"/></svg>
          <span>GeraldFenwickPhotography47@mailbox.test</span>
        </li>
        <li class="contact__item">
          <svg class="contact__icon" viewBox="0 0 24 24" aria-hidden="true"><circle cx="12" cy="12" r="10" fill="#fff"/><path d="M2 12h20M12 2c3 3 3 17 0 20M12 2c-3 3-3 17 0 20" fill="none" stroke="#8d8d8d" stroke-width="1.4"/></svg>
          <span>www.GeraldFenwickPhotography.test.au</span>
        </li>
        <li class="contact__item">
          <span class="contact__social-mark" aria-hidden="true"></span>
          <span>_Gerald_fenwick</span>
        </li>
      </ul>
    </div>
  </section>

  <section class="card card--logo" aria-label="Business card, logo side">
    <div class="brand">
      <span class="brand__dot"></span>
      <span class="brand__name">Gerald Fenwick<br>Photography</span>
    </div>
  </section>
</main>
</body>
</html>
```